Fitness Equipment & Service

I want to make the card eye catching and fun. We are called Corvane Motion Limited and we are based in Wales. We sell, install and service all types of fitness equipment from Skipping ropes, right through the Dumbbells, Kettle bells and Barbells through to state of the art Treadmills, Running Machines and Strength Equipment. We also design and install changing room furniture and lockers.

TYPOGRAPHY
We would like to use Futrura. Futura has an appearance of efficiency and forwardness. The typeface is derived
from simple geometric forms (near-perfect circles, triangles and squares) and is based on strokes of
near-even weight, which are low in contrast. This is most visible in the almost perfectly round stroke of
the o, which is nonetheless slightly ovoid.
The lowercase has tall ascenders, which rise above the cap line. The uppercase
characters present proportions similar to those of classical Roman capitals.

TYPOGRAPHIC CONSIDERATIONS
No Strike though
No Horizontal Scaling
No Drop Shadows
No Effects
Never use less than 120% Leading

OUR CORPORATE COLOURS
BRAND GUIDELINES
We were thinking that our primary colour palette consists of the Acid Green (Pantone 382) and Process Black.

We work closely with tquarly Ltd and would like to include their name on the card somewhere. I have attached images of the other brands that we work with as an idea or the small icons I have included that illustrate what we do?. I have very kindly been given permission to use any of the images off the files that I have included below, so I hope these help. I will include these below. I would be open to suggestions if it made the card more striking Can you do it?
Updates

Hi All, Just wanted to add a few thoughts but you are the guys with the creative visions (thats why are here) We are based in Wales, UK and we would be open to lots of different ideas on a theme but must be eye catching, Bold and FUN. If you can or think that the Welsh or any dragon could be put in there then go for it (its not a must have) We have also added some ideas for colour but again its over to you!! GO FOR IT ! Thanks and look forward to your visions! Owen

Hi All, Just thought I would sen through the contact details that need to be on the card. (if you want to play around with icons instead of the wording twitter, Facebook, go for it): Corvane Motion Limited Owen Pritchard Managing Director Mob: +44 (0)7582 913 406 e-mail: sales@corvanemotion.co.uk Web: Corvanemotion.co.uk twitter: @motionLetterbin Facebook: Corvane Motion Limited

```html
<!DOCTYPE html>
<html lang="en">
<head>
<meta charset="utf-8">
<title>Corvane Motion Limited – Business Card</title>
<link href="https://fonts.googleapis.com/css2?family=Open+Sans:wght@400;700&family=Exo+2:wght@700&display=swap" rel="stylesheet">
<style>
  :root {
    --page: #eceef1;
    --card: #ffffff;
    --navy: #1b2350;
    --band-dark: #1e2f6e;
    --band-light: #2f6cb4;
    --tile-blue: #2a88d0;
    --tile-sky: #4fb6e8;
    --tile-deep: #1f6a99;
    --tile-ink: #1d3a5a;
    --tile-grey: #8e9ba6;
    --photo-a: #0d1e3d;
    --photo-b: #1d4a86;
    --white: #ffffff;
  }
  * { margin: 0; padding: 0; box-sizing: border-box; }
  html, body { width: 1200px; height: 1000px; overflow: hidden; }
  body { background: var(--page); position: relative; font-family: "Open Sans", Arial, sans-serif; }

  .card { position: absolute; left: 265px; width: 666px; height: 397px; background: var(--card); overflow: hidden; box-shadow: 0 2px 6px rgba(0,0,0,.12); }
  .card--front { top: 73px; }
  .card--back { top: 532px; }

  .edge-bar { position: absolute; left: 0; top: 82px; width: 25px; height: 233px; background: var(--navy); }

  .brand-mark { position: absolute; left: 90px; top: 75px; width: 210px; text-align: center; }
  .brand-mark__dot { width: 120px; height: 120px; border-radius: 50%; background: var(--band-dark); margin: 0 auto 26px; }
  .brand-mark__name { font-weight: 700; font-size: 22px; line-height: 1.25; color: var(--navy); }

  .band { position: absolute; left: 365px; width: 301px; background: linear-gradient(90deg, var(--band-dark), var(--band-light)); color: var(--white); }
  .band--name { top: 79px; height: 62px; padding: 6px 0 0 13px; }
  .band--contact { top: 158px; height: 80px; padding: 7px 0 0 14px; }
  .band--social { top: 253px; height: 62px; padding: 9px 0 0 14px; }

  .holder-name { font-weight: 700; font-size: 21px; line-height: 1.25; letter-spacing: .3px; }
  .holder-role { font-size: 15px; line-height: 1.25; }

  .contact-line { display: flex; align-items: center; font-size: 15.5px; line-height: 1.4; }
  .contact-line svg { width: 13px; height: 13px; margin-right: 9px; flex: none; }
  .contact-line .plain-dot { width: 8px; height: 8px; border-radius: 50%; background: var(--white); margin: 0 12px 0 2px; flex: none; }

  .mosaic { position: absolute; left: 0; top: 53px; width: 666px; height: 292px;
    background: linear-gradient(120deg, var(--photo-a), var(--photo-b) 55%, var(--photo-a)); }
  .tile { position: absolute; width: 95px; height: 97px; display: flex; align-items: center; justify-content: center; }
  .tile svg { width: 56px; height: 56px; }
  .t-blue { background: var(--tile-blue); }
  .t-sky { background: var(--tile-sky); }
  .t-deep { background: var(--tile-deep); }
  .t-ink { background: var(--tile-ink); }
  .t-grey { background: var(--tile-grey); }

  .partner { position: absolute; left: 296px; top: 117px; color: var(--white); text-align: right; width: 258px; }
  .partner__name { font-family: "Exo 2", "Open Sans", sans-serif; font-weight: 700; font-size: 47px; line-height: 1.2; letter-spacing: 1px; }
  .partner__tagline { font-family: "Exo 2", "Open Sans", sans-serif; font-weight: 700; font-size: 15px; line-height: 1.25; letter-spacing: .5px; }
</style>
</head>
<body>

<section class="card card--front">
  <div class="edge-bar"></div>
  <div class="brand-mark">
    <div class="brand-mark__dot"></div>
    <div class="brand-mark__name">Corvane Motion Limited</div>
  </div>

  <div class="band band--name">
    <div class="holder-name">OWEN PRITCHARD</div>
    <div class="holder-role">Managing Director</div>
  </div>

  <div class="band band--contact">
    <div class="contact-line">
      <svg viewBox="0 0 12 16"><rect x="2" y="0.8" width="8" height="14.4" rx="1.5" fill="none" stroke="#fff" stroke-width="1.4"/><circle cx="6" cy="12.6" r="0.9" fill="#fff"/></svg>
      +44 (0)7582 913 406
    </div>
    <div class="contact-line">
      <svg viewBox="0 0 16 12"><rect x="0.7" y="0.7" width="14.6" height="10.6" fill="none" stroke="#fff" stroke-width="1.4"/><path d="M1 1l7 6 7-6" fill="none" stroke="#fff" stroke-width="1.4"/></svg>
      sales@corvanemotion.co.uk
    </div>
    <div class="contact-line">
      <svg viewBox="0 0 16 14"><rect x="0.7" y="0.7" width="14.6" height="9.6" fill="none" stroke="#fff" stroke-width="1.4"/><path d="M5 13.3h6M8 10.3v3" stroke="#fff" stroke-width="1.4"/></svg>
      Corvanemotion.co.uk
    </div>
  </div>

  <div class="band band--social">
    <div class="contact-line"><span class="plain-dot"></span>@motionLetterbin</div>
    <div class="contact-line"><span class="plain-dot"></span>Corvane Motion Limited</div>
  </div>
</section>

<section class="card card--back">
  <div class="mosaic" role="img" aria-label="Gym floor photograph with treadmills and exercise bikes in blue tones">
    <!-- row 1 -->
    <div class="tile t-blue" style="left:0;top:0">
      <svg viewBox="0 0 56 56"><rect x="4" y="10" width="48" height="30" fill="none" stroke="#fff" stroke-width="4"/><circle cx="28" cy="25" r="8" fill="none" stroke="#fff" stroke-width="2.5"/><path d="M20 25h16M28 17v16" stroke="#fff" stroke-width="2"/><path d="M20 48h16M28 40v8" stroke="#fff" stroke-width="4"/></svg>
    </div>
    <div class="tile t-sky" style="left:95px;top:0" role="img" aria-label="Floor plan icon"></div>
    <div class="tile" style="left:190px;top:0" role="img" aria-label="Exercise bike icon"></div>
    <div class="tile t-ink" style="left:285px;top:0" role="img" aria-label="Lockers icon"></div>
    <div class="tile t-blue" style="left:380px;top:0" role="img" aria-label="Treadmill icon"></div>
    <div class="tile t-deep" style="left:475px;top:0">
      <svg viewBox="0 0 56 56"><circle cx="28" cy="31" r="16" fill="none" stroke="#fff" stroke-width="4"/><path d="M24 9h8M28 9v6M28 31V22" stroke="#fff" stroke-width="4"/></svg>
    </div>
    <div class="tile" style="left:570px;top:0;width:96px" role="img" aria-label="Boxing gloves icon"></div>
    <!-- row 2 -->
    <div class="tile" style="left:0;top:97px" role="img" aria-label="Gift voucher icon"></div>
    <div class="tile t-grey" style="left:95px;top:97px" role="img" aria-label="Kettlebell icon"></div>
    <div class="tile t-blue" style="left:190px;top:97px" role="img" aria-label="Minibus icon"></div>
    <div class="tile t-ink" style="left:570px;top:97px;width:96px">
      <svg viewBox="0 0 56 56"><path d="M6 28h6l4-8 5 16 5-12 4 8 4-10 5 14 4-8h7" fill="none" stroke="#fff" stroke-width="3"/></svg>
    </div>
    <!-- row 3 -->
    <div class="tile t-deep" style="left:190px;top:195px" role="img" aria-label="Weight bench icon"></div>
    <div class="tile t-sky" style="left:380px;top:195px" role="img" aria-label="Card terminal icon"></div>
    <div class="tile t-grey" style="left:475px;top:195px" role="img" aria-label="Class presentation icon"></div>

    <div class="partner">
      <div class="partner__name">TQUARLY</div>
      <div class="partner__tagline">MAKING CLUBS EFFICIENT</div>
    </div>
  </div>
</section>

</body>
</html>
```